U.S. Popcorn company needs business cards

We are a popcorn company that manufactures popcorn and sells it to grocery stores worldwide. Our theme is "Americana" and our logo is U.S. route 66 which is the most famous highway in the U.S.

We would like the design to be simple and to use both sides. On the back side we would like to see just the logo and website. The front would be normal details

Target Market(s)

Wholesalers, grocers and distributors

Industry/Entity Type

Manufacture

Contact Information for Business Card

Business name: Prairie Lantern Popcorn
Phone: +1 555 308 4726
Email: Dale@prairielanternpopcorn.com
website: www.prairielanternpopcorn.com
Tag Line: "POPular for a reason"
Name: Dale Whitcombe
Title: Founder/President

Requirements
Must have
• Either this design should be fun or clean and simple. I will let you show me your thougths.
Nice to have
• Anything that ties in the real Hwy Route 66.
• Colors might need to be red, white and blue incorporated.
Should not have
• Not be too busy.

```html
<!DOCTYPE html>
<html lang="en">
<head>
<meta charset="utf-8">
<title>Prairie Lantern Popcorn – Business Cards</title>
<link href="https://fonts.googleapis.com/css2?family=Lato:wght@400;700&display=swap" rel="stylesheet">
<style>
  :root {
    --stage: #222222;
    --navy: #232f64;
    --red: #e01f26;
    --white: #ffffff;
    --ink: #232f64;
  }
  * { margin: 0; padding: 0; box-sizing: border-box; }
  html, body { width: 1189px; height: 1200px; overflow: hidden; }
  body {
    background: var(--stage);
    font-family: "Lato", Arial, sans-serif;
    position: relative;
  }
  .card {
    position: absolute;
    left: 171px;
    width: 855px;
    height: 487px;
    border-radius: 25px;
    overflow: hidden;
    box-shadow: 0 4px 10px rgba(0,0,0,0.45);
  }
  .card--front { top: 68px; background: var(--navy); color: var(--white); text-align: center; }
  .card--back { top: 627px; background: var(--white); color: var(--ink); }

  .brand-title {
    position: absolute; left: 0; right: 0; top: 236px;
    font-size: 54px; font-weight: 700; letter-spacing: 0.5px;
    line-height: 1;
  }
  .tagline {
    position: absolute; left: 0; right: 0; top: 346px;
    font-size: 23px; font-weight: 400;
  }

  .wordmark {
    position: absolute; left: 66px; width: 340px; top: 160px;
    text-align: center; font-size: 38px; font-weight: 700;
    line-height: 1.15; color: var(--navy);
  }
  .divider {
    position: absolute; left: 407px; top: 93px;
    width: 2px; height: 253px; background: var(--red);
  }
  .contact { position: absolute; left: 462px; top: 88px; }
  .contact__name { font-size: 34px; font-weight: 400; line-height: 1; color: var(--navy); }
  .contact__role { font-size: 23px; color: var(--red); line-height: 1.1; margin-top: 2px; }
  .contact__address { font-size: 23px; line-height: 29px; margin-top: 40px; }
  .contact__list { list-style: none; margin-top: 12px; }
  .contact__list li {
    display: flex; align-items: center; gap: 10px;
    font-size: 21px; height: 29px;
  }
  .icon { width: 25px; height: 25px; flex: none; }
  .wave { position: absolute; left: 0; top: 0; width: 855px; height: 487px; }
</style>
</head>
<body>

  <section class="card card--front">
    <h1 class="brand-title">PRAIRIE LANTERN POPCORN</h1>
    <p class="tagline">POPular for a reason</p>
  </section>

  <section class="card card--back">
    <div class="wordmark">Prairie Lantern Popcorn</div>
    <div class="divider"></div>

    <div class="contact">
      <p class="contact__name">Dale Whitcombe</p>
      <p class="contact__role">Founder/President</p>
      <p class="contact__address">Harlow Bend, KS<br>United States</p>
      <ul class="contact__list">
        <li>
          <svg class="icon" viewBox="0 0 25 25" aria-hidden="true">
            <rect width="25" height="25" rx="3" fill="#e01f26"/>
            <path d="M8 5.5 L10.5 5 L12 9 L10.3 10.3 C11 12.5 12.5 14 14.7 14.7 L16 13 L20 14.5 L19.5 17 C13 18 7 12 8 5.5 Z" fill="#fff"/>
          </svg>
          +1 555 308 4726
        </li>
        <li>
          <svg class="icon" viewBox="0 0 25 25" aria-hidden="true">
            <rect width="25" height="25" rx="3" fill="#e01f26"/>
            <rect x="5" y="7.5" width="15" height="10" fill="none" stroke="#fff" stroke-width="1.5"/>
            <path d="M5 7.5 L12.5 13 L20 7.5" fill="none" stroke="#fff" stroke-width="1.5"/>
          </svg>
          Dale@prairielanternpopcorn.com
        </li>
        <li>
          <svg class="icon" viewBox="0 0 25 25" aria-hidden="true">
            <rect width="25" height="25" rx="3" fill="#e01f26"/>
            <circle cx="12.5" cy="12.5" r="7" fill="none" stroke="#fff" stroke-width="1.4"/>
            <ellipse cx="12.5" cy="12.5" rx="3" ry="7" fill="none" stroke="#fff" stroke-width="1.2"/>
            <path d="M5.5 12.5 H19.5 M6.5 9 H18.5 M6.5 16 H18.5" stroke="#fff" stroke-width="1.1"/>
          </svg>
          www.prairielanternpopcorn.com
        </li>
      </ul>
    </div>

    <svg class="wave" viewBox="0 0 855 487" aria-hidden="true">
      <path d="M0 376 C220 455 430 470 620 412 C730 380 800 366 845 368 C790 374 720 390 620 426 C430 490 200 472 0 386 Z" fill="#e01f26"/>
      <path d="M0 394 C210 480 430 494 625 438 C730 404 800 390 855 392 L855 487 L0 487 Z" fill="#232f64"/>
    </svg>
  </section>

</body>
</html>
```